New Business Card Design Project LORVANTI-Italy

we are LORVANTI-Italy
our company in the market for 3 years we are luxury cosmetic company and its about time for a facelift :)
i will like to have elegant luxurious and unique business card
that will give the person that get it a unique, luxurious and elegant impression
I'm VERY OPEN FOR NEW IDEAS , even duo i add a few files of things that i see on line and i like them

i add my logo as well
my website is LORVANTI.COM
(if you would like to see the main style that we have)

Target Market(s)

adult that have money :)

Industry/Entity Type

Business

Contact Information for Business Card

Name - Dario Lorvanti
Position - CEO and CO Founder
address - 4817 E Halvern
telephone - 555-384-1926
email - dario@lorvanti.com
fax - 555-384-1926
website - LORVANTI.COM

Colors
000000
959595
fbee3e
ffffff

Requirements
Must have
• big logo in GOLD color
• elegant look
• impressive
Nice to have
• not must but maybe classy pattern background
• not must but maybe emblem
• maybe clear plastic business card
Should not have
• colors
• images

```html
<!DOCTYPE html>
<html lang="en">
<head>
<meta charset="utf-8">
<title>LORVANTI Italy – Business Card</title>
<link href="https://fonts.googleapis.com/css2?family=Tinos:wght@400;700&family=Source+Sans+3:wght@400&display=swap" rel="stylesheet">
<style>
  :root{
    --backdrop-top:#d6d6d6;
    --backdrop-bottom:#ffffff;
    --card-black:#0b0b0b;
    --card-edge:#1a1a1a;
    --gold:#d8b23c;
    --gold-light:#ecd06a;
    --gold-deep:#b58c22;
    --band-grey:#4a4a4a;
    --band-grey-dark:#262626;
    --ink-white:#f2f2f2;
    --icon-ink:#0b0b0b;
  }
  *{margin:0;padding:0;box-sizing:border-box}
  html,body{width:1200px;height:900px;overflow:hidden}
  body{
    position:relative;
    background:linear-gradient(to bottom,var(--backdrop-top) 0%,var(--backdrop-bottom) 100%);
    font-family:"Source Sans 3",Arial,sans-serif;
  }
  .card{
    position:absolute;
    top:184px;
    height:490px;
    border-radius:12px;
    background:var(--card-black);
    box-shadow:0 0 0 1px var(--card-edge);
    overflow:hidden;
  }
  .card--front{left:299px;width:301px}
  .card--back{left:645px;width:305px}

  /* front */
  .front-decor{position:absolute;left:186px;top:276px;width:220px;height:220px}
  .brand-emblem{position:absolute;left:95px;top:37px;width:106px;height:106px}
  .brand-name{
    position:absolute;left:0;right:0;top:166px;
    text-align:center;
    font-family:"Tinos","Times New Roman",serif;
    font-size:44px;font-weight:400;letter-spacing:1px;
    color:var(--gold);line-height:1;
  }
  .brand-rule{
    position:absolute;left:32px;top:218px;width:233px;height:2px;
    background:var(--gold);
  }
  .brand-origin{
    position:absolute;left:0;right:0;top:227px;
    text-align:center;
    font-family:"Tinos","Times New Roman",serif;
    font-size:18px;letter-spacing:1px;color:var(--gold);
  }
  .person-name{
    position:absolute;left:31px;top:292px;
    font-family:"Tinos","Times New Roman",serif;
    font-size:19px;font-weight:700;color:var(--gold-light);letter-spacing:.3px;
  }
  .person-title{
    position:absolute;left:31px;top:315px;
    font-size:13.5px;color:var(--ink-white);
  }
  .contact-list{
    position:absolute;left:30px;top:349px;list-style:none;
  }
  .contact-list li{
    display:flex;align-items:center;height:20.5px;
    font-size:13.5px;color:var(--ink-white);
  }
  .contact-list svg{width:15px;height:15px;margin-right:8px;flex:none}
  .address{
    position:absolute;left:28px;top:441px;
    font-size:13.5px;color:var(--ink-white);
  }

  /* back */
  .back-band{position:absolute;left:-98px;top:-4px;width:500px;height:500px}
  .back-emblem{position:absolute;left:50px;top:144px;width:206px;height:206px}
  .back-name{
    position:absolute;left:0;right:0;top:230px;
    text-align:center;
    font-family:"Tinos","Times New Roman",serif;
    font-size:32px;color:var(--card-black);letter-spacing:1px;line-height:1;
  }
</style>
</head>
<body>

<section class="card card--front" aria-label="Business card front">
  <svg class="front-decor" viewBox="0 0 220 220" role="img" aria-label="Faint dark decorative ring pattern">
    <defs>
      <radialGradient id="faintRing" cx="50%" cy="50%" r="50%">
        <stop offset="70%" stop-color="#1a1a1a"/>
        <stop offset="100%" stop-color="#121212"/>
      </radialGradient>
    </defs>
    <circle cx="110" cy="110" r="92" fill="none" stroke="url(#faintRing)" stroke-width="30"/>
  </svg>

  <svg class="brand-emblem" viewBox="0 0 106 106" role="img" aria-label="Brand emblem area">
    <defs>
      <radialGradient id="goldDiscFront" cx="40%" cy="35%" r="70%">
        <stop offset="0%" stop-color="var(--gold-light)"/>
        <stop offset="100%" stop-color="var(--gold-deep)"/>
      </radialGradient>
    </defs>
    <circle cx="53" cy="53" r="52" fill="url(#goldDiscFront)"/>
  </svg>
  <div class="brand-name">LORVANTI</div>
  <div class="brand-rule"></div>
  <div class="brand-origin">ITALY</div>

  <div class="person-name">DARIO LORVANTI</div>
  <div class="person-title">CEO and CO Founder</div>

  <ul class="contact-list">
    <li>
      <svg viewBox="0 0 16 16" aria-hidden="true"><circle cx="8" cy="8" r="8" fill="var(--gold)"/><path d="M4 6.5c0-1.5 8-1.5 8 0v1h-2.2v-1H6.2v1H4zM5 8.5h6l1 3H4z" fill="var(--icon-ink)"/></svg>
      555-384-1926
    </li>
    <li>
      <svg viewBox="0 0 16 16" aria-hidden="true"><circle cx="8" cy="8" r="8" fill="var(--gold)"/><rect x="5.5" y="3.5" width="5" height="3" fill="var(--icon-ink)"/><rect x="4" y="7" width="8" height="4.5" rx="1" fill="var(--icon-ink)"/></svg>
      555-384-1926
    </li>
    <li>
      <svg viewBox="0 0 16 16" aria-hidden="true"><circle cx="8" cy="8" r="8" fill="var(--gold)"/><rect x="4" y="5" width="8" height="6" fill="var(--icon-ink)"/><path d="M4 5l4 3.2L12 5" fill="none" stroke="var(--gold)" stroke-width="1"/></svg>
      dario@lorvanti.com
    </li>
    <li>
      <svg viewBox="0 0 16 16" aria-hidden="true"><circle cx="8" cy="8" r="8" fill="var(--gold)"/><circle cx="8" cy="8" r="4" fill="none" stroke="var(--icon-ink)" stroke-width="1.3"/><path d="M4 8h8M8 4c-2 2.5-2 5.5 0 8M8 4c2 2.5 2 5.5 0 8" fill="none" stroke="var(--icon-ink)" stroke-width="1"/></svg>
      LORVANTI.COM
    </li>
  </ul>
  <div class="address">4817 E Halvern</div>
</section>

<section class="card card--back" aria-label="Business card back">
  <svg class="back-band" viewBox="0 0 500 500" role="img" aria-label="Large grey decorative ring pattern around the emblem">
    <defs>
      <linearGradient id="bandTone" x1="0" y1="0" x2="1" y2="1">
        <stop offset="0%" stop-color="var(--band-grey)"/>
        <stop offset="50%" stop-color="var(--band-grey-dark)"/>
        <stop offset="100%" stop-color="var(--band-grey)"/>
      </linearGradient>
    </defs>
    <circle cx="250" cy="250" r="210" fill="none" stroke="url(#bandTone)" stroke-width="62"/>
  </svg>

  <svg class="back-emblem" viewBox="0 0 206 206" role="img" aria-label="Brand emblem area">
    <defs>
      <radialGradient id="goldDiscBack" cx="40%" cy="35%" r="70%">
        <stop offset="0%" stop-color="var(--gold-light)"/>
        <stop offset="100%" stop-color="var(--gold-deep)"/>
      </radialGradient>
    </defs>
    <circle cx="103" cy="103" r="102" fill="url(#goldDiscBack)"/>
  </svg>
  <div class="back-name">LORVANTI</div>
</section>

</body>
</html>
```